$5 Quest Website Required

I am looking for someone to develop a website akin to the simplicity of www.boxlantern.example with a video in the center or a tab that permits one to "Accept the Challenge."

Incorporates our logo and is used to promote our "$5 Quest Program."

Please see attachments, but we are igniting entrepreneurial spirit among our nation's youth through this interactive and intensive program!

There should be a way to navigate to other sections of the site including:

About
Why
Request $5 Quest Packet
Success Stories
Partners
Link to Norvik Holdings
Updates

Thanks to all in advance!

Looking forward to working with you!

Good feel of what we are looking for in terms of "feel"

http://www.thebrightripple.example/

Thank you,

RB

Please make note of this website, we are going for a feel that is akin to this and less modern and professional...more abstract and interactive...but of course include space for our video:

Colors, feel, imagery, is great. Keep your formats, but bring on the feel!

Thank you all for your hard work and patience.

Thank you all for your hard work thus far.

Meanwhile, please understand that the $5 Quest is young, youthful, full of challenge and vitality, it is a competition among students from high school and universities.  The websites you have delivered are too corporate, stale, and standard.  I'm looking for something that is fresh, different, like www.thebrightripple.example.

Symbols, cartoonish, but serious, down to business and save the world one $5 bill at a time.  The logo can be used as a theme...the colors, the feel.

Video space for explanation on the $5 Quest front and center.  With leaves, $ signs, colorful colors, etc.

Visual needs to be compelling to Join the Challenge! Although Norvik Holdings and the tree is a parent company; $5 Quest is separate and Norvik Holdings should only be mentioned as a link.

PixelHarbor.example in regard to simplicity; and www.thebrightripple.example in terms of style.

Thank you,

Raphael

Like the designs that have been submitted; we are almost there.

Target Market(s)

Professors, students, teachers, parents and NGO leaders who wish to use our program as a way to inspire leadership/entrepreneurship/fundraise for their causes.

Requirements
Must have
• Place for the video, front and center
Include logo
Forsight for blogging, message, etc.
Nice to have
• Plan "buckets" to include"
Explanation Video
Two pamphlets
Contract
FAQs
Website with Blog, voting, registration, video upload, etc.
Flyer perfected
Parable...symbol of our life
Photos
Stats included
Testimonials
Organizations that have used (TKWLM, North Brook Lodge, Marlowton High)
Sponsors (Open Lantern, Copperleaf Learningfield)
Photos from events

I understand this takes coding and such, but want you to be aware of the long term vision for it!

```html
<!DOCTYPE html>
<html lang="en">
<head>
<meta charset="utf-8">
<title>$5 Quest — Home</title>
<link href="https://fonts.googleapis.com/css2?family=Roboto+Condensed:wght@400;700&family=Arimo:wght@400&family=PT+Sans:wght@400&display=swap" rel="stylesheet">
<style>
:root{
  --paper:#f7eedb;
  --paper-deep:#efe2c6;
  --paper-light:#fbf5e8;
  --green:#0f9440;
  --green-dark:#0b7a34;
  --orange:#f7931e;
  --gray-text:#555555;
  --body-text:#333333;
  --gold-line:#f2cf4a;
  --frame-gray:#dcdcdc;
  --white:#ffffff;
}
*{margin:0;padding:0;box-sizing:border-box}
html,body{width:1200px;height:896px;overflow:hidden}
body{position:relative;background:var(--paper);font-family:"Arimo",Arial,sans-serif;color:var(--body-text)}
.backdrop{position:absolute;inset:0;
  background:
    radial-gradient(ellipse 320px 520px at 1090px 560px,rgba(200,190,170,.45),transparent 70%),
    radial-gradient(ellipse 520px 420px at 560px 380px,var(--paper-light),transparent 75%),
    linear-gradient(180deg,var(--paper-light),var(--paper) 55%,var(--paper-deep));}
.abs{position:absolute}

.utility{top:0;left:852px;display:flex;align-items:center;font-family:"Roboto Condensed",sans-serif;font-weight:700;font-size:14px;letter-spacing:.5px;color:#222}
.utility a{color:#222;text-decoration:none;padding:5px 9px 0}
.utility .signin{background:#f1ede4}
.language{margin-left:8px;background:var(--green);color:var(--white);font-size:12px;height:26px;width:96px;display:flex;align-items:center;justify-content:space-between;padding:0 8px;border-radius:0 0 3px 3px}

.brand{top:42px;left:330px;display:flex;align-items:center;gap:22px}
.brand-dot{width:110px;height:110px;border-radius:50%;background:var(--green)}
.brand-name{font-family:"PT Sans",sans-serif;font-size:74px;color:#4a4a4a;line-height:1}

.main-nav{top:211px;left:0;width:1070px;display:flex;justify-content:center;align-items:center;font-family:"Roboto Condensed",sans-serif;font-size:20px;letter-spacing:.4px;color:#555}
.main-nav a{color:#555;text-decoration:none}
.main-nav a.active{color:var(--green);font-weight:700}
.main-nav .sep{width:5px;height:5px;border-radius:50%;background:var(--green-dark);margin:0 20px}
.nav-rule{top:250px;left:22px;width:1044px;height:1px;background:var(--gold-line)}

.section-title{font-family:"PT Sans",sans-serif;font-size:20px;letter-spacing:.3px}
.section-title .o{color:var(--orange)} .section-title .g{color:var(--green)}
.dots{height:0;border-top:1px dotted #666}

.welcome{top:298px;left:22px;width:285px}
.welcome .dots{margin:8px 0 16px}
.welcome p{font-size:13.5px;line-height:19.5px;text-align:justify;margin-bottom:7px}

.video-card{top:271px;left:358px;width:482px;height:402px;border:1px solid var(--gold-line);border-radius:8px;padding:5px;background:rgba(255,255,255,.35)}
.video-screen{width:100%;height:100%;background:var(--white);border:6px solid var(--frame-gray);border-radius:4px;position:relative;box-shadow:0 30px 22px -22px rgba(0,0,0,.35)}
.watch-label{position:absolute;top:278px;left:0;width:100%;text-align:center;font-family:"Roboto Condensed",sans-serif;font-size:28px;color:#222;letter-spacing:.3px}
.play{position:absolute;left:156px;top:75px}

.testimonials{top:298px;left:880px;width:185px}
.testimonials .dots{margin:8px 0 16px}
.quote{font-size:13.5px;line-height:17.5px;text-align:justify;width:157px;margin-left:9px}
.quote + .author{margin-top:10px}
.author{text-align:right;font-size:13px;color:var(--gray-text)}
.testimonials .author{margin-bottom:22px}

.cta-line{top:743px;height:0;border-top:2px dashed var(--green)}
.cta{top:714px;left:402px}
.cta-text{position:absolute;top:714px;left:402px;width:361px;height:59px;display:flex;align-items:center;justify-content:center;color:var(--white);font-family:"PT Sans",sans-serif;font-size:22px;letter-spacing:.3px}

.footer-rule{top:818px;left:22px;width:1042px;border-top:2px dotted #cfc8b8}
.footer-brand{top:845px;left:36px;display:flex;align-items:center;gap:6px}
.footer-brand .dot{width:22px;height:22px;border-radius:50%;background:var(--green)}
.footer-brand span{font-family:"PT Sans",sans-serif;font-size:21px;color:#4a4a4a}
.footer-nav{top:838px;right:149px;display:flex;gap:18px;font-size:12px}
.footer-nav a{color:#222;text-decoration:none}
.copyright{top:862px;right:149px;font-size:12px;color:#222}
</style>
</head>
<body>
<div class="backdrop" role="img" aria-label="Warm paper texture with faint hand-drawn words, arrows and doodles about success, and a soft photo of a businessman at the right edge"></div>

<div class="abs utility">
  <a href="#">FAQ</a>
  <a href="#" class="signin">SIGNIN</a>
  <span class="language">LANGUAGE <svg width="11" height="9" viewBox="0 0 11 9"><path d="M0 0h11L5.5 9z" fill="#fff"/></svg></span>
</div>

<div class="abs brand">
  <div class="brand-dot"></div>
  <div class="brand-name">$5 Quest</div>
</div>

<nav class="abs main-nav">
  <a href="#" class="active">HOME</a><span class="sep"></span>
  <a href="#">ABOUT US</a><span class="sep"></span>
  <a href="#">WHY WE ARE?</a><span class="sep"></span>
  <a href="#">SUCCESS STORIES</a><span class="sep"></span>
  <a href="#">PARTNERS</a><span class="sep"></span>
  <a href="#">NORVIK HOLDINGS</a>
</nav>
<div class="abs nav-rule"></div>

<section class="abs welcome">
  <h2 class="section-title"><span class="o">WELCOME TO</span> <span class="g">$5 QUEST</span></h2>
  <div class="dots"></div>
  <p>Lorem ipsum dolor sit amet, consectetur adipiscing elit. Curabitur eu nisl odio. Cras egestas turpis in mi feugiat vel tincidunt arcu accumsan. Phasellus non posuere eros. Aenean consectetur.</p>
  <p>sapien in elit luctus ac posuere purus placerat. Aliquam turpis lorem,.</p>
  <p>Donec fermentum sodales erat, quis consequat nisi ornare eget. Duis volutpat justo ut ante imperdiet feugiat. fermentum sodales erat, quis consequat nisi ornare eget. Duis volutpat justo ut ante imperdiet feugiat.</p>
  <p>sapien in elit luctus ac posuere purus placerat. Aliquam turpis lorem,.</p>
</section>

<div class="abs video-card">
  <div class="video-screen">
    <svg class="play" width="158" height="158" viewBox="0 0 158 158">
      <defs><linearGradient id="playFill" x1="0" y1="0" x2="0" y2="1"><stop offset="0" stop-color="#111"/><stop offset="1" stop-color="#3a3a3a"/></linearGradient></defs>
      <circle cx="79" cy="79" r="78" fill="url(#playFill)"/>
      <path d="M63 48 L103 79 L63 110 Z" fill="#bdbdbd"/>
    </svg>
    <div class="watch-label">WATCH VIDEO</div>
  </div>
</div>

<aside class="abs testimonials">
  <h2 class="section-title" style="margin-left:9px"><span class="g">Client</span> <span class="o">Testimonials</span></h2>
  <div class="dots"></div>
  <p class="quote">Lorem ipsum dolor sit amsectetur adipiscing elit. Curabitur eu nisl odio. dolor sit amsectetur u nisl odio.</p>
  <p class="author">- LOREM IPSUM</p>
  <p class="quote" style="margin-left:6px">Lorem ipsum dolor sit amsectetur adipiscing elit. Curabitur eu nisl odio. dolor sit amsectetur u nisl odio.</p>
  <p class="author">- LOREM IPSUM</p>
</aside>

<div class="abs cta-line" style="left:275px;width:138px"></div>
<div class="abs cta-line" style="left:750px;width:152px"></div>
<svg class="abs cta" width="361" height="59" viewBox="0 0 361 59">
  <path d="M0 0 H361 L344 29.5 L361 59 H0 L17 29.5 Z" fill="var(--green)"/>
</svg>
<a class="cta-text" href="#">ACCEPT THE CHALLENGE</a>

<div class="abs footer-rule"></div>
<div class="abs footer-brand"><span class="dot"></span><span>$5 Quest</span></div>
<nav class="abs footer-nav">
  <a href="#">Home</a><a href="#">About Us</a><a href="#">Success Stories</a><a href="#">Partners</a><a href="#">Norvik Holdings</a><a href="#">Terms</a><a href="#">Privacy Policy</a>
</nav>
<p class="abs copyright">All Rights reserved @ $5quest</p>
</body>
</html>
```